Bar and Grill needs specials signage

I have attached a file called "daily specials" I need it changed - so there is 1 sign/poster for each day/special
also attached other items to show some styling. I want the new posters chalkboard format, styled along the lines of the drink designs attached.
The designs should be scaleable, and editable, I will print locally

```html
<!DOCTYPE html>
<html lang="en">
<head>
<meta charset="utf-8">
<title>Daily Specials – Monday</title>
<link href="https://fonts.googleapis.com/css2?family=Fredericka+the+Great&family=Pacifico&family=Cabin+Sketch:wght@700&family=Gochi+Hand&display=swap" rel="stylesheet">
<style>
  :root {
    --board-dark: #2b302c;
    --board-mid: #3c413d;
    --board-light: #5a5e5a;
    --chalk: #f4f4f0;
    --chalk-teal: #7fcfd4;
    --chalk-orange: #e8832a;
    --art-tone: #4a4f4b;
  }
  html, body { margin: 0; padding: 0; overflow: hidden; background: var(--board-dark); }
  .poster {
    position: relative;
    width: 927px;
    height: 1200px;
    overflow: hidden;
    background:
      radial-gradient(ellipse 45% 35% at 55% 38%, var(--board-light) 0%, transparent 100%),
      radial-gradient(ellipse 70% 55% at 50% 50%, var(--board-mid) 0%, var(--board-dark) 100%);
    color: var(--chalk);
  }
  .board-frame { position: absolute; inset: 0; }
  .corner-ornament {
    position: absolute; width: 46px; height: 46px;
    background: radial-gradient(circle, rgba(244,244,240,.45), rgba(244,244,240,0) 70%);
  }
  .corner-ornament.tl { left: 34px; top: 26px; }
  .corner-ornament.tr { right: 34px; top: 26px; }
  .corner-ornament.bl { left: 34px; bottom: 26px; }
  .corner-ornament.br { right: 34px; bottom: 26px; }
  .eyebrow {
    position: absolute; left: 146px; width: 640px; top: 86px;
    margin: 0; text-align: center; white-space: nowrap;
    font-family: "Fredericka the Great", serif;
    font-weight: 400; font-size: 64px; line-height: 1; letter-spacing: 1px;
  }
  .day {
    position: absolute; left: 150px; width: 640px; top: 150px;
    margin: 0; text-align: center; white-space: nowrap;
    font-family: "Pacifico", cursive;
    font-weight: 400; font-size: 140px; line-height: 1.2;
  }
  .illustration {
    position: absolute; left: 384px; top: 416px; width: 300px; height: 496px;
    border-radius: 40px;
    background: radial-gradient(ellipse at 50% 45%, var(--art-tone), transparent 72%);
  }
  .offer {
    position: absolute; left: 150px; top: 0; margin: 0;
    font-family: "Cabin Sketch", sans-serif; font-weight: 700;
    color: var(--chalk-teal); line-height: 1;
  }
  .offer span { position: absolute; left: 0; white-space: nowrap; }
  .offer .kids { top: 456px; font-size: 100px; letter-spacing: 2px; }
  .offer .eat  { top: 544px; font-size: 100px; letter-spacing: 18px; }
  .offer .free { top: 642px; left: 8px; font-size: 76px; letter-spacing: 13px; }
  .terms {
    position: absolute; left: 40px; width: 847px; top: 920px;
    margin: 0; text-align: center; white-space: nowrap;
    font-family: "Gochi Hand", cursive;
    font-size: 90px; line-height: 80px;
  }
  .terms span { display: block; }
</style>
</head>
<body>
<main class="poster">
  <svg class="board-frame" width="927" height="1200" viewBox="0 0 927 1200" aria-hidden="true">
    <rect x="42" y="34" width="843" height="1132" fill="none" stroke="var(--chalk)" stroke-width="4"/>
    <rect x="49" y="41" width="829" height="1118" fill="none" stroke="var(--chalk)" stroke-width="1.5" opacity=".5"/>
    <g stroke="var(--chalk)" stroke-linecap="round" fill="none">
      <line x1="178" y1="376" x2="776" y2="374" stroke-width="4"/>
      <line x1="152" y1="408" x2="612" y2="406" stroke-width="4"/>
    </g>
    <g stroke="var(--chalk-orange)" stroke-width="3" stroke-linecap="round">
      <line x1="110" y1="180" x2="136" y2="190"/>
      <line x1="86" y1="257" x2="128" y2="257"/>
      <line x1="110" y1="332" x2="136" y2="324"/>
      <line x1="794" y1="190" x2="820" y2="180"/>
      <line x1="806" y1="257" x2="848" y2="257"/>
      <line x1="794" y1="324" x2="820" y2="332"/>
    </g>
  </svg>

  <div class="corner-ornament tl" role="img" aria-label="Chalk flourish ornament"></div>
  <div class="corner-ornament tr" role="img" aria-label="Chalk flourish ornament"></div>
  <div class="corner-ornament bl" role="img" aria-label="Chalk flourish ornament"></div>
  <div class="corner-ornament br" role="img" aria-label="Chalk flourish ornament"></div>

  <h2 class="eyebrow">DAILY SPECIALS</h2>
  <h1 class="day">Monday</h1>

  <div class="illustration" role="img" aria-label="Chalk drawing of a child at a table eating a plate of food with a fork"></div>

  <svg class="board-frame" width="927" height="1200" viewBox="0 0 927 1200" aria-hidden="true">
    <g fill="none" stroke="var(--chalk-orange)" stroke-width="2.5" stroke-linejoin="round">
      <path d="M768 446 L776 464 Q730 500 718 540 L736 546 L694 580 L680 526 L698 532 Q712 486 768 446 Z" fill="rgba(232,131,42,.25)"/>
      <path d="M226 740 L244 734 Q262 770 268 800 L282 794 L268 830 L240 808 L254 804 Q246 772 226 740 Z" fill="rgba(232,131,42,.25)"/>
    </g>
  </svg>

  <p class="offer">
    <span class="kids">KIDS</span>
    <span class="eat">EAT</span>
    <span class="free">FREE</span>
  </p>

  <p class="terms">
    <span>From our kids menu,</span>
    <span>for adult purchase</span>
  </p>
</main>
</body>
</html>
```